Bicycle dealer and service & repair center

The registered brand of our company, Rad Lindhof, means bicycle of the city Zurich (Switzerland) and is the largest dealer of e-bikes, folding bikes and cargo bikes in Switzerland. Rad Lindhof also sells a substantial amount of road bikes, mountainbikes, trailers and bicycles without electric motor. The more, we are known for special bikes (tandems, Swiss military bicycles, postman bicycles, and others).Rad Lindhof has around 10 highly skilled employees and runs a well-equipped service & repair center. We have around 50 brand dealerships for replacement parts, diagnostic devices and are proud about our after-sales service.Our website is fully functional (see www.rad-lindhof.ch) and available in three languages (DE, EN, FR for the french speaking part of Switzerland). Live stock information is provided by https://www.rad-lindhof.ch/en/rad.We need a redesign of our website. The focus should be on:- e-catalog with simple search and extended search - e-commerce (e.g. add to chart, favorites, text search, filter, sort, related products, similar products, most popular search, related articles, top listings, promotions...)- cross-selling with our affiliated company Rad Brunnegg, our bicycle shop in a city nearby Zurich.- service and repair- company (sustainable business, emission-free mobility, public relation, well-trained and friendly staff)- mobile friendlyness- maximize usability- maximize usage of display for useful information- easy to find relevant information- simple search functionalityKey audience is:- middle to high-price bicycle customers- existing and returning clients- prospective employees- members of the pressThe goal of the website and its redesign is:- increase the number of enquiries via website- increase online sales- share information with others (addtoany)- provide information about the right selection of bicycle (faq, detailed information about components) to reduce the admin associated with new enquiries- highlight special offers (e.g. free bicycle service slots, sunday exhibition)As Rad Lindhof has many returning customers and already high website traffic (according to SERP), the new design should be a smooth transition from the existing website.Websites we like:- https://tramofix.ch/- https://www.kurbelhaus.ch/- https://www.quandor.ch/- https://www.autoscout24.ch/deGood luck and have fun creating our new design!
Updates

website we also like: https://www.pedalora.ch/

Target Market(s)

Urban bicycle riders

Industry/Entity Type

Retail

Coding

Coded - Design and coding required

Number of Pages Required

5+ page

Font styles to use
Other font styles liked:
• Avenir (https://www.glyphbazar.com/fonts/typecraft/avenir/)

Colors

Designer to choose colors to be used in the design.

Requirements
Must have
• The actual content www.rad-lindhof.ch must be published with the new website design. Additional content should be added according to project description (see above).
Nice to have
• - we use the font type Avenir (https://www.glyphbazar.com/fonts/typecraft/avenir/) for business cards, leaflets etc
Should not have
• Frippery

```html
<!DOCTYPE html>
<html lang="en">
<head>
<meta charset="utf-8">
<title>Rad Lindhof – E-Bikes, Cargobikes, Velos</title>
<link rel="stylesheet" href="https://fonts.googleapis.com/css2?family=Nunito+Sans:wght@400;600;700;800&family=Oswald:wght@600&display=swap">
<style>
:root{
  --blue:#1d6fa5;
  --blue-dark:#175a88;
  --blue-line:#2b7fb5;
  --text:#333;
  --muted:#777;
  --card:#f2f2f2;
  --border:#dcdcdc;
  --panel:#dfeaf2;
  --footer:#3a3a3a;
  --footer-bottom:#2c2c2c;
  --footer-text:#b5b5b5;
  --red:#d8322b;
}
*{box-sizing:border-box;margin:0;padding:0}
html,body{width:1200px;height:3382px;overflow:hidden}
body{position:relative;background:#fff;font-family:"Nunito Sans",sans-serif;color:var(--text)}
.abs{position:absolute}
a{color:inherit;text-decoration:none}
.icon{width:12px;height:12px;fill:currentColor;flex:none}

/* header */
.site-header{left:0;top:0;width:1200px;height:87px;background:#fff}
.brand{left:144px;top:20px;display:flex;align-items:center;gap:10px}
.brand-name{font-weight:800;font-size:30px;letter-spacing:-.5px;color:#111;line-height:1}
.brand-mark{width:40px;height:40px;background:var(--blue);border-radius:5px}
.brand-tag{left:144px;top:57px;font-size:8px;color:#333}
.main-nav{left:450px;top:37px;font-size:11px;color:#555}
.main-nav a{position:absolute;white-space:nowrap}
.main-nav .active{color:var(--blue)}
.search{left:727px;top:25px;width:218px;height:38px;border:1px solid #ccc;border-radius:2px;display:flex;align-items:center;padding:0 14px;font-size:12px;color:#888;justify-content:space-between}
.round-btn{top:24px;width:42px;height:42px;border:1px solid #bbb;border-radius:50%;display:flex;align-items:center;justify-content:center;color:#777}
.round-btn .icon{width:15px;height:15px}

/* hero */
.hero{left:0;top:87px;width:1200px;height:528px;background:linear-gradient(180deg,#4b5d72 0%,#7b7c80 30%,#c0824a 55%,#e98a2e 66%,#8a4e26 80%,#3b2618 100%)}
.hero-title{left:144px;top:168px;color:#fff;font-size:25px;font-weight:700;line-height:37px;text-transform:uppercase;letter-spacing:.3px}
.btn{background:var(--blue);color:#fff;font-weight:700;font-size:13px;text-transform:uppercase;display:flex;align-items:center;justify-content:center}
.hero-btn{left:144px;top:323px;width:104px;height:38px}
.hero-arrow{top:332px;width:24px;height:36px;background:rgba(60,60,60,.7);border:1px solid rgba(255,255,255,.4);display:flex;align-items:center;justify-content:center}
.hero-arrow svg{width:10px;height:16px;stroke:#fff;fill:none;stroke-width:1.5}

/* section heads */
.section-title{left:143px;font-size:29px;color:var(--blue);font-weight:400;line-height:1}
.view-all{left:737px;width:70px;height:28px;background:#cfcfcf;color:#555;font-size:10px;text-transform:uppercase;display:flex;align-items:center;justify-content:center}

/* product cards */
.card-row{left:144px;width:663px;height:401px}
.product-card{position:absolute;top:0;width:214px;height:401px;background:var(--card);border:1px solid var(--border)}
.product-media{position:absolute;left:8px;top:8px;width:198px;height:176px;background:radial-gradient(ellipse at center,#d9dcdf 0%,#f3f4f5 55%,#fff 75%)}
.save-note{position:absolute;left:8px;bottom:6px;font-size:12px;color:var(--red)}
.product-brand{position:absolute;left:8px;top:189px;font-size:13px;font-weight:800;color:#222;text-transform:uppercase;letter-spacing:.5px}
.product-name{position:absolute;left:8px;top:213px;font-size:13px;color:var(--blue)}
.product-price{position:absolute;left:8px;top:236px;font-size:13px;color:#222}
.card-btn{position:absolute;left:8px;width:198px;height:34px;background:#fff;border:1px solid #ccc;font-size:11px;color:#555;text-transform:uppercase;display:flex;align-items:center;gap:12px;padding-left:12px}
.card-btn.info{top:270px}
.card-btn.cart{top:313px}
.card-btn.fav{top:356px}

/* stock banner */
.stock-banner{left:144px;top:1191px;width:663px;height:335px;background:linear-gradient(135deg,#8c8e93 0%,#5d6068 40%,#44495a 70%,#6e4a4a 100%)}
.stock-text{left:293px;top:1351px;font-family:"Oswald",sans-serif;font-weight:600;font-size:50px;line-height:61px;color:#fff}
.stock-btn{left:502px;top:1421px;width:103px;height:39px}

/* similar product */
.similar{left:144px;top:2071px;width:663px;height:334px;background:var(--panel)}
.similar-media{left:170px;top:2085px;width:330px;height:300px;background:radial-gradient(ellipse at center,#bcc8cf 0%,#d3dfe6 45%,rgba(223,234,242,0) 72%)}
.similar-title{left:550px;top:2105px;font-size:31px;color:var(--blue);line-height:1}
.similar-brand{left:550px;top:2160px;height:20px;padding:0 4px;border:1px solid #333;font-size:11px;line-height:18px;color:#222;text-transform:uppercase}
.similar-price{left:549px;top:2190px;font-size:46px;color:#222;line-height:1.1;white-space:nowrap}
.similar-note{left:550px;top:2245px;font-size:13px;color:#222}
.similar-btn{left:550px;top:2279px;width:103px;height:39px}
.pager{top:2343px;width:23px;height:21px;border:1px solid #888;display:flex;align-items:center;justify-content:center}
.pager svg{width:6px;height:10px;stroke:#555;fill:none;stroke-width:1.4}

/* sidebar */
.filter-box{left:838px;width:218px;background:var(--blue)}
.filter-head{height:52px;background:var(--blue-dark);color:#fff;font-size:21px;display:flex;align-items:center;padding-left:15px}
.filter-item{height:40px;border-top:1px solid var(--blue-line);display:flex;align-items:center;gap:11px;padding-left:16px;font-size:12px;color:#fff;white-space:nowrap}
.filter-item::before{content:"";width:12px;height:12px;background:#fff;flex:none}
.price-field{margin:0 14px 14px;height:34px;background:#fff;display:flex;align-items:center;justify-content:space-between;padding:0 14px;font-size:12px;color:#555}
.more-filters{left:838px;top:1539px;font-size:11px;color:#555;text-transform:uppercase}
.aside-title{left:837px;top:1578px;font-size:22px;color:var(--blue);font-weight:400}
.article-media{left:838px;top:1622px;width:218px;height:147px;background:linear-gradient(160deg,#8d9a6b 0%,#5a6d75 40%,#3a4452 70%,#a9a06a 100%)}
.article-title{left:838px;top:1779px;width:220px;font-size:16px;line-height:22px;color:var(--blue);font-weight:400}
.article-date{left:838px;top:1856px;font-size:11px;color:#222}
.article-text{left:838px;top:1881px;width:218px;font-size:10px;line-height:17px;color:#555}
.article-btn{left:838px;top:1951px;width:89px;height:38px}

/* footer */
.site-footer{left:0;top:2974px;width:1200px;height:312px;background:var(--footer)}
.footer-col{top:3011px;color:var(--footer-text);font-size:10.5px;line-height:17.5px}
.footer-col h3{font-size:18px;font-weight:400;color:#fff;margin-bottom:8px;line-height:20px}
.footer-col ul{list-style:none}
.footer-col li::before{content:"•";margin-right:6px}
.gap{height:17px}
.footer-bottom{left:0;top:3286px;width:1200px;height:96px;background:var(--footer-bottom)}
.footer-nav{left:144px;top:3311px;font-size:11px;color:var(--footer-text)}
.footer-nav span{margin:0 8px}
.copyright{left:144px;top:3340px;font-size:11px;color:var(--footer-text)}
.social{top:3327px;width:14px;height:14px;border-radius:50%;background:#9a9a9a}
</style>
</head>
<body>
<svg width="0" height="0" style="position:absolute">
  <symbol id="i-eye" viewBox="0 0 24 24"><path d="M12 5C6 5 2 12 2 12s4 7 10 7 10-7 10-7-4-7-10-7zm0 11a4 4 0 110-8 4 4 0 010 8zm0-6a2 2 0 100 4 2 2 0 000-4z"/></symbol>
  <symbol id="i-cart" viewBox="0 0 24 24"><path d="M2 3h3l1 3h15l-3 8H8l-1 2h12v2H4l3-5L4 5H2zM8 20a2 2 0 104 0 2 2 0 00-4 0zm7 0a2 2 0 104 0 2 2 0 00-4 0z"/></symbol>
  <symbol id="i-heart" viewBox="0 0 24 24"><path d="M12 21l-1.5-1.3C5 15 2 12 2 8a5 5 0 019-3 5 5 0 019 3c0 4-3 7-8.5 11.7z"/></symbol>
  <symbol id="i-search" viewBox="0 0 24 24"><path d="M10 3a7 7 0 015.6 11.2l5.6 5.6-1.4 1.4-5.6-5.6A7 7 0 1110 3zm0 2a5 5 0 100 10 5 5 0 000-10z"/></symbol>
</svg>

<!-- Header -->
<header class="abs site-header">
  <div class="abs brand"><span class="brand-name">RAD LINDHOF</span><span class="brand-mark"></span></div>
  <div class="abs brand-tag">E-Bikes | Cargobikes | Velos | Service &amp; Reparaturen</div>
  <nav class="abs main-nav">
    <a class="active" style="left:0">Velos</a>
    <a style="left:50px">Services</a>
    <a style="left:115px">News</a>
    <a style="left:166px">About Us</a>
    <a style="left:235px">FAQ</a>
  </nav>
  <div class="abs search">Search <svg class="icon" style="width:15px;height:15px;color:#888"><use href="#i-search"/></svg></div>
  <div class="abs round-btn" style="left:958px"><svg class="icon"><use href="#i-heart"/></svg></div>
  <div class="abs round-btn" style="left:1014px"><svg class="icon"><use href="#i-cart"/></svg></div>
</header>

<!-- Hero -->
<section class="abs hero" role="img" aria-label="Photo of a cyclist with an e-bike on a hilltop at sunset"></section>
<h1 class="abs hero-title">With 1082 vehicles, Switzerland's<br>largest selection of e-bikes,<br>transport bikes and<br>folding bikes.</h1>
<a class="abs btn hero-btn">Shop now</a>
<div class="abs hero-arrow" style="left:0"><svg viewBox="0 0 10 16"><path d="M8 1L2 8l6 7"/></svg></div>
<div class="abs hero-arrow" style="left:1176px"><svg viewBox="0 0 10 16"><path d="M2 1l6 7-6 7"/></svg></div>

<!-- Top Listings -->
<h2 class="abs section-title" style="top:692px">Top Listings</h2>
<a class="abs view-all" style="top:697px">View all</a>
<div class="abs card-row" style="top:741px">
  <article class="product-card" style="left:0">
    <div class="product-media" role="img" aria-label="Photo of a black gravel bike"></div>
    <div class="product-brand">Ardel</div><div class="product-name">Crosspoint AL 4</div><div class="product-price">CHF 1'859.-</div>
    <a class="card-btn info"><svg class="icon"><use href="#i-eye"/></svg>View more information</a>
    <a class="card-btn cart"><svg class="icon"><use href="#i-cart"/></svg>Add to cart</a>
    <a class="card-btn fav"><svg class="icon"><use href="#i-heart"/></svg>Add to favorites</a>
  </article>
  <article class="product-card" style="left:225px">
    <div class="product-media" role="img" aria-label="Photo of a blue child bike trailer"></div>
    <div class="product-brand">Norvik</div><div class="product-name">Crosspoint AL 4</div><div class="product-price">CHF 1'859.-</div>
    <a class="card-btn info"><svg class="icon"><use href="#i-eye"/></svg>View more information</a>
    <a class="card-btn cart"><svg class="icon"><use href="#i-cart"/></svg>Add to cart</a>
    <a class="card-btn fav"><svg class="icon"><use href="#i-heart"/></svg>Add to favorites</a>
  </article>
  <article class="product-card" style="left:449px">
    <div class="product-media" role="img" aria-label="Photo of a dark road bike"></div>
    <div class="product-brand">Kestra</div><div class="product-name">Crosspoint AL 4</div><div class="product-price">CHF 1'859.-</div>
    <a class="card-btn info"><svg class="icon"><use href="#i-eye"/></svg>View more information</a>
    <a class="card-btn cart"><svg class="icon"><use href="#i-cart"/></svg>Add to cart</a>
    <a class="card-btn fav"><svg class="icon"><use href="#i-heart"/></svg>Add to favorites</a>
  </article>
</div>

<!-- Stock banner -->
<section class="abs stock-banner" role="img" aria-label="Photo of the shop floor with rows of e-bikes in stock"></section>
<div class="abs stock-text">Über 400 E-Bikes<br>an Lager!</div>
<a class="abs btn stock-btn">Shop now</a>

<!-- Most Popular -->
<h2 class="abs section-title" style="top:1572px">Most Popular Products</h2>
<a class="abs view-all" style="top:1577px">View all</a>
<div class="abs card-row" style="top:1622px">
  <article class="product-card" style="left:0">
    <div class="product-media" role="img" aria-label="Photo of a black gravel bike"></div>
    <div class="product-brand">Ardel</div><div class="product-name">Crosspoint AL 4</div><div class="product-price">CHF 1'859.-</div>
    <a class="card-btn info"><svg class="icon"><use href="#i-eye"/></svg>View more information</a>
    <a class="card-btn cart"><svg class="icon"><use href="#i-cart"/></svg>Add to cart</a>
    <a class="card-btn fav"><svg class="icon"><use href="#i-heart"/></svg>Add to favorites</a>
  </article>
  <article class="product-card" style="left:225px">
    <div class="product-media" role="img" aria-label="Photo of a folded e-bike"></div>
    <div class="product-brand">Falco</div><div class="product-name">Crosspoint AL 4</div><div class="product-price">CHF 1'859.-</div>
    <a class="card-btn info"><svg class="icon"><use href="#i-eye"/></svg>View more information</a>
    <a class="card-btn cart"><svg class="icon"><use href="#i-cart"/></svg>Add to cart</a>
    <a class="card-btn fav"><svg class="icon"><use href="#i-heart"/></svg>Add to favorites</a>
  </article>
  <article class="product-card" style="left:449px">
    <div class="product-media" role="img" aria-label="Photo of a bamboo city bike"><span class="save-note">You save CHF 93.-</span></div>
    <div class="product-brand">Corvo</div><div class="product-name">Crosspoint AL 4</div><div class="product-price">CHF 1'859.-</div>
    <a class="card-btn info"><svg class="icon"><use href="#i-eye"/></svg>View more information</a>
    <a class="card-btn cart"><svg class="icon"><use href="#i-cart"/></svg>Add to cart</a>
    <a class="card-btn fav"><svg class="icon"><use href="#i-heart"/></svg>Add to favorites</a>
  </article>
</div>

<!-- Similar product -->
<section class="abs similar"></section>
<div class="abs similar-media" role="img" aria-label="Photo of a lime green folding bike"></div>
<h2 class="abs similar-title" style="font-weight:400">Similar Product</h2>
<div class="abs similar-brand">Hollis</div>
<div class="abs similar-price">CHF 1'850</div>
<div class="abs similar-note">Incl. Additional equipment</div>
<a class="abs btn similar-btn">Shop now</a>
<div class="abs pager" style="left:550px"><svg viewBox="0 0 6 10"><path d="M5 1L1 5l4 4"/></svg></div>
<div class="abs pager" style="left:580px"><svg viewBox="0 0 6 10"><path d="M1 1l4 4-4 4"/></svg></div>

<!-- Related Products -->
<h2 class="abs section-title" style="top:2443px">Related Products</h2>
<a class="abs view-all" style="top:2449px">View all</a>
<div class="abs card-row" style="top:2493px">
  <article class="product-card" style="left:0">
    <div class="product-media" role="img" aria-label="Photo of a bamboo city bike"></div>
    <div class="product-brand">Corvo</div><div class="product-name">Crosspoint AL 4</div><div class="product-price">CHF 1'859.-</div>
    <a class="card-btn info"><svg class="icon"><use href="#i-eye"/></svg>View more information</a>
    <a class="card-btn cart"><svg class="icon"><use href="#i-cart"/></svg>Add to cart</a>
    <a class="card-btn fav"><svg class="icon"><use href="#i-heart"/></svg>Add to favorites</a>
  </article>
  <article class="product-card" style="left:225px">
    <div class="product-media" role="img" aria-label="Photo of a red and black folding bike"></div>
    <div class="product-brand">Vanta</div><div class="product-name">Crosspoint AL 4</div><div class="product-price">CHF 1'859.-</div>
    <a class="card-btn info"><svg class="icon"><use href="#i-eye"/></svg>View more information</a>
    <a class="card-btn cart"><svg class="icon"><use href="#i-cart"/></svg>Add to cart</a>
    <a class="card-btn fav"><svg class="icon"><use href="#i-heart"/></svg>Add to favorites</a>
  </article>
  <article class="product-card" style="left:449px">
    <div class="product-media" role="img" aria-label="Photo of a blue trekking bike"></div>
    <div class="product-brand">Alpwind</div><div class="product-name">Crosspoint AL 4</div><div class="product-price">CHF 1'859.-</div>
    <a class="card-btn info"><svg class="icon"><use href="#i-eye"/></svg>View more information</a>
    <a class="card-btn cart"><svg class="icon"><use href="#i-cart"/></svg>Add to cart</a>
    <a class="card-btn fav"><svg class="icon"><use href="#i-heart"/></svg>Add to favorites</a>
  </article>
</div>

<!-- Sidebar filters -->
<aside>
  <div class="abs filter-box" style="top:695px">
    <div class="filter-head">Power</div>
    <div class="filter-item">E-bike up to 25 km / h (598)</div>
    <div class="filter-item">E-bike up to 45 km / h (146)</div>
    <div class="filter-item">Bike without engine</div>
    <div class="filter-item">Bike without engine</div>
  </div>
  <div class="abs filter-box" style="top:927px">
    <div class="filter-head">Type</div>
    <div class="filter-item">City / Trekkingbike (49)</div>
    <div class="filter-item">Faltvelo (193)</div>
    <div class="filter-item">Transport wheel 2-wheel (4)</div>
    <div class="filter-item">Transport wheel 3-wheel (1)</div>
    <div class="filter-item">Military Bike (13)</div>
    <div class="filter-item">Tandem (6)</div>
    <div class="filter-item">Mountain bike (4)</div>
    <div class="filter-item">Racing Bike (34)</div>
    <div class="filter-item">Velo Trailer (34)</div>
  </div>
  <div class="abs filter-box" style="top:1359px;height:167px">
    <div class="filter-head" style="margin-bottom:15px">Price</div>
    <div class="price-field"><span>Min</span><span>$</span></div>
    <div class="price-field"><span>Max</span><span>$</span></div>
  </div>
  <a class="abs more-filters">View more filters »</a>
  <h2 class="abs aside-title">Related Articles</h2>
  <div class="abs article-media" role="img" aria-label="Photo of an e-bike ridden on a forest trail"></div>
  <h3 class="abs article-title">Etiam vel massa elementum, bibendum tellus venenatis, feugiat massa</h3>
  <div class="abs article-date">20 MAY, 2019</div>
  <p class="abs article-text">Maecenas vel tortor accumsan quam varius imperdiet vel eget elit. Aenean facilisis tincidunt lectus, id dictum nisi luctus eget.</p>
  <a class="abs btn article-btn">View all</a>
</aside>

<!-- Footer -->
<footer>
  <div class="abs site-footer"></div>
  <div class="abs footer-col" style="left:144px;width:230px">
    <h3>Contact Info</h3>
    Rad Lindhof GmbH<br>Lindenweg 12, CH-8999 Zürich<br>+41 (0)44 000 12 34<br>info@rad-lindhof.ch
    <div class="gap"></div>VAT number CHE-000.123.456
    <div class="gap"></div>For parking possibilities please ask at the<br>shop.
    <div class="gap"></div>Public transportation: bus no. 12 / no 14<br>exit bus station "Lindenplatz"
  </div>
  <div class="abs footer-col" style="left:424px">
    <h3>Bank Details</h3>
    Swiss postal account: 80-000000-1<br>IBAN: CH00 0000 0000 0000 0000 0<br>BIC: LNDHCHZZXXX<br>BC: 9000
    <div class="gap"></div>Customs account: 20001-1
  </div>
  <div class="abs footer-col" style="left:704px">
    <h3>Payment Methods</h3>
    <ul><li>Postal debit card</li><li>Debit card CH</li><li>Bank transfer in advance</li><li>Cash (only Swiss Francs)</li></ul>
    <div class="gap"></div>We do not accept credit cards.
  </div>
  <div class="abs footer-col" style="left:969px">
    <h3>Languages</h3>
    <ul><li>English</li><li>Français</li><li>Deutsch</li></ul>
    <div class="gap"></div><div class="gap"></div>Folgen Sie uns
  </div>
  <div class="abs footer-bottom"></div>
  <nav class="abs footer-nav">Velos<span>|</span>Services<span>|</span>News<span>|</span>About Us<span>|</span>FAQ</nav>
  <div class="abs copyright">Copyright © 2019 Rad Lindhof GmbH. &nbsp; All rights reserved.</div>
  <span class="abs social" style="left:965px" aria-label="Social profile"></span>
  <span class="abs social" style="left:999px" aria-label="Social profile"></span>
  <span class="abs social" style="left:1039px" aria-label="Video channel"></span>
</footer>
</body>
</html>
```